Corporate brochure design 4 pages

Hi,

We are a real estate company based in Europe.

We have almost finalized a rebranding.

We are developing a brand book guidelines (still on working process) to help you undertstand the look and feel of our new CI. I would like to receive proposals of design for a corporate brochure template. I need to receive the Indesign files with full ownership rights to be able to adapt all our documentation with this template.
Regarding the images, you can take gabaris on www.pelvarimages.example. I will be able to take them afterwards.

There will be 4 pages. you will receive the 4 pages on pdf for your consideration with our (almost) actual layout.

- 1st page: cover
- 2nd page: company presentation in french and english
- 3rd page: some market data + graph
- 4th page: 2 retail centers presentation.

In the template, i need to have:
- the paragraph styles in order
- 2 different masters with top/bottom/page number aso.

Please feel free to ask any other questions.

best regards,
Updates

I would like to precise tha t we are active on the commercial real estate sector:

- office transactions (rent /sales)
- property management of administrative and business buildings
- Valuation of properties
- Capital markets (investment advices for selling building)

Industry/Entity Type

Real Estate

Colors

Designer to choose colors to be used in the design.

```html
<!DOCTYPE html>
<html lang="en">
<head>
<meta charset="utf-8">
<title>Meridian Estates – About us &amp; Office Market Report</title>
<link rel="stylesheet" href="https://fonts.googleapis.com/css2?family=Arimo:ital,wght@0,400;0,700;1,400&display=swap">
<style>
  :root {
    --blue: #1a7fa9;
    --orange: #e5622c;
    --bar: #0b4a67;
    --white: #ffffff;
    --photo-a: #8a9398;
    --photo-b: #3b4046;
  }
  * { margin: 0; padding: 0; box-sizing: border-box; }
  html, body { width: 1200px; height: 849px; overflow: hidden; }
  body { font-family: "Arimo", Arial, sans-serif; color: var(--white); position: relative; background: var(--blue); }

  .block { position: absolute; }
  .bg-blue { background: var(--blue); }
  .bg-orange { background: var(--orange); }

  .section-bar {
    position: absolute; height: 24px; background: var(--bar);
    font-weight: 700; font-size: 11.5px; line-height: 24px; padding-left: 8px; letter-spacing: .2px;
  }
  .subhead { position: absolute; font-weight: 700; font-size: 12px; }
  .body-copy { position: absolute; font-size: 10px; line-height: 17.2px; }

  .team-photo { position: absolute; left: 43px; top: 479px; width: 514px; height: 302px;
    background: linear-gradient(160deg, var(--photo-a), var(--photo-b)); }
  .caption { position: absolute; left: 43px; width: 514px; top: 792px; text-align: center; font-style: italic; font-size: 9.5px; }

  .stock-table { position: absolute; left: 626px; top: 256px; width: 574px; font-size: 9px; }
  .stock-table .head, .stock-table .total-bar { background: var(--bar); height: 16px; font-weight: 700; }
  .row { position: relative; height: 13px; line-height: 13px; }
  .row span, .head span, .total-bar span { position: absolute; white-space: nowrap; }
  .head span, .total-bar span { line-height: 16px; }
  .c-region { left: 5px; }
  .c-label { left: 140px; }
  .c-district { left: 181px; }
  .c-stock { right: 172px; text-align: right; }
  .c-pct { right: 52px; text-align: right; }
  .head .c-stock { right: 168px; }
  .head .c-pct { right: 52px; }
  .gap { height: 13px; }
  .total-bar { margin-top: 6px; }

  .chart { position: absolute; left: 750px; top: 615px; }
  .chart text { font-family: "Arimo", Arial, sans-serif; fill: var(--white); }
  .legend-key { position: absolute; left: 790px; top: 768px; width: 22px; height: 20px; background: var(--white); }
  .legend-label { position: absolute; left: 792px; top: 789px; font-size: 7px; font-style: italic; }
  .source { position: absolute; left: 1063px; top: 792px; font-size: 8px; font-style: italic; }
  .brand { position: absolute; left: 1098px; top: 793px; display: flex; align-items: center; gap: 3px; font-size: 7.5px; font-weight: 700; color: var(--bar); line-height: 8px; }
  .brand i { width: 9px; height: 9px; background: var(--bar); display: block; }
</style>
</head>
<body>
  <!-- background panels -->
  <div class="block bg-orange" style="left:0;top:252px;width:435px;height:597px"></div>
  <div class="block bg-orange" style="left:763px;top:0;width:437px;height:608px"></div>

  <!-- left page -->
  <div class="section-bar" style="left:35px;top:38px;width:498px">ABOUT US</div>
  <div class="subhead" style="left:43px;top:73px">A TEAM</div>
  <p class="body-copy" style="left:43px;top:91px;width:500px">Our ambition is to offer quality services that perfectly meet your expectations. This ambition is shared by all members of the team.<br>Thanks to our knowledge of the Luxembourg market, our skills and our commitment to the missions entrusted to us, Meridian Estates is the undisputed leader in commercial real estate in the Grand Duchy. We are proud of this position and work hard to deserve it every day.<br>Targeting excellence means the constant improvement of our services in order to more accurately meet your needs. When you meet with us, you will find that our employees take the necessary time to listen to you and to correctly understand your need. Their professionalism, know-how and mobilisation will ensure that we find the right solution.</p>

  <div class="section-bar" style="left:35px;top:265px;width:498px">A PROPOS DE NOUS</div>
  <div class="subhead" style="left:43px;top:300px">UNE ÉQUIPE</div>
  <p class="body-copy" style="left:43px;top:318px;width:505px">Proposer des services de qualité répondant parfaitement à vos attentes est notre ambition. Elle est partagée par tous les membres de notre équipe.<br>Notre connaissance du marché luxembourgeois, nos compétences et notre engagement dans les missions qui nous sont confiées font de Meridian Estates l’acteur majeur de l’immobilier d’entreprise au Grand-Duché. Nous sommes fiers de cette position et nous travaillons tous les jours pour la conserver.<br>Viser l’excellence suppose de savoir améliorer sans cesse nos prestations pour répondre le plus précisément à vos besoins. Venez nous consulter, vous constaterez que nos collaborateurs prennent le temps de vous écouter pour bien comprendre votre demande. Leur professionnalisme, leur savoir-faire et leur mobilisation nous permettront de trouver la solution.</p>

  <div class="team-photo" role="img" aria-label="Group portrait of the four partners in business suits in an office lobby"></div>
  <div class="caption">Laurent Meyers, Olivier Danlot, Paul Kessing, Henri Valmont</div>

  <!-- right page -->
  <div class="section-bar" style="left:626px;top:38px;width:574px">LUXEMBOURG OFFICE MARKET REPORT Q3-2013</div>
  <div class="subhead" style="left:635px;top:83px">STOCK</div>
  <p class="body-copy" style="left:635px;top:102px;width:520px">The stock of available office square meters has increased by 0.36% during the third quarter of this year with the delivery of 12,300 m². The total stock reaches 3,465,600 sm².</p>

  <div class="section-bar" style="left:626px;top:150px;width:574px">RAPPORT DE MARCHÉ BUREAUX LUXEMBOURG</div>
  <div class="subhead" style="left:635px;top:187px">STOCK</div>
  <p class="body-copy" style="left:635px;top:207px;width:545px">Le stock de mètres carrés disponibles de bureaux a augmenté de 0,36 % au troisième trimestre de cette année grâce à la livraison de près de 12 300 m². Le stock total équivaut à 3 465 600 m².</p>

  <div class="stock-table">
    <div class="head"><span class="c-district">QUARTIERS-DISTRICTS</span><span class="c-stock">STOCK M²</span><span class="c-pct">STOCK%</span></div>
    <div class="row" style="margin-top:4px"><span class="c-region">CENTRE-VILLE (CITY)</span><span class="c-district">Kirchberg</span><span class="c-stock">915 000</span><span class="c-pct">26,42 %</span></div>
    <div class="row"><span class="c-district">CBD</span><span class="c-stock">806 400</span><span class="c-pct">23,27 %</span></div>
    <div class="row"><span class="c-district">Station</span><span class="c-stock">382 700</span><span class="c-pct">11,04 %</span></div>
    <div class="row"><span class="c-district">Cloche d’Or</span><span class="c-stock">365 600</span><span class="c-pct">10,55 %</span></div>
    <div class="row"><span class="c-district">Limpertsberg</span><span class="c-stock">85 000</span><span class="c-pct">2,45 %</span></div>
    <div class="row"><span class="c-district">Belair / Merl</span><span class="c-stock">67 800</span><span class="c-pct">1,96 %</span></div>
    <div class="row"><span class="c-district">Hamm</span><span class="c-stock">44 500</span><span class="c-pct">1,28 %</span></div>
    <div class="row"><span class="c-district">Kalchesbrück</span><span class="c-stock">33 000</span><span class="c-pct">0,95 %</span></div>
    <div class="row"><span class="c-label">TOTAL</span><span class="c-stock">2 700 500</span><span class="c-pct">77,92 %</span></div>
    <div class="gap"></div>
    <div class="row"><span class="c-region">VILLE-PÉRIPHÉRIE (CITY-PERIPHERY)</span><span class="c-district">Airport - Findel</span><span class="c-stock">157 500</span><span class="c-pct">4,54 %</span></div>
    <div class="row"><span class="c-district">Bertrange / Bourmicht</span><span class="c-stock">82 000</span><span class="c-pct">2,37 %</span></div>
    <div class="row"><span class="c-district">Strassen</span><span class="c-stock">81 050</span><span class="c-pct">2,34 %</span></div>
    <div class="row"><span class="c-district">Howald</span><span class="c-stock">62 600</span><span class="c-pct">1,81 %</span></div>
    <div class="row"><span class="c-district">TOTAL</span><span class="c-stock">383 150</span><span class="c-pct">11,06 %</span></div>
    <div class="row"><span class="c-region">PÉRIPHÉRIE (PERIPHERY)</span><span class="c-district">Belval</span><span class="c-stock">93 090</span><span class="c-pct">2,69 %</span></div>
    <div class="row"><span class="c-district">Capellen</span><span class="c-stock">69 500</span><span class="c-pct">2,01 %</span></div>
    <div class="row"><span class="c-district">Leudelange</span><span class="c-stock">73 556</span><span class="c-pct">2,12 %</span></div>
    <div class="row"><span class="c-district">Munsbach</span><span class="c-stock">60 100</span><span class="c-pct">1,73 %</span></div>
    <div class="row"><span class="c-district">Windhof</span><span class="c-stock">40 800</span><span class="c-pct">1,17 %</span></div>
    <div class="row"><span class="c-district">Esch-sur-Alzette</span><span class="c-stock">24 700</span><span class="c-pct">0,71 %</span></div>
    <div class="row"><span class="c-district">Contern</span><span class="c-stock">20 400</span><span class="c-pct">0,59 %</span></div>
    <div class="row"><span class="c-label">TOTAL</span><span class="c-stock">381 946</span><span class="c-pct">11,02 %</span></div>
    <div class="total-bar"><span class="c-label">TOTAL</span><span class="c-stock">3 465 596</span></div>
  </div>

  <svg class="chart" width="350" height="150" viewBox="0 0 350 150" role="img" aria-label="Bar chart of office stock 2003 to YTD 2013">
    <g stroke="#cfe3ec" stroke-width=".6" stroke-dasharray="3 2" fill="none">
      <line x1="32" y1="9" x2="340" y2="9"/><line x1="32" y1="27.3" x2="340" y2="27.3"/>
      <line x1="32" y1="45.7" x2="340" y2="45.7"/><line x1="32" y1="64" x2="340" y2="64"/>
      <line x1="32" y1="82.3" x2="340" y2="82.3"/><line x1="32" y1="100.7" x2="340" y2="100.7"/>
      <line x1="32" y1="119" x2="340" y2="119"/><line x1="340" y1="9" x2="340" y2="125"/>
      <line x1="33" y1="9" x2="33" y2="125"/>
    </g>
    <g font-size="7" text-anchor="end">
      <text x="28" y="11">3.500</text><text x="28" y="29.5">3.200</text><text x="28" y="48">2.900</text>
      <text x="28" y="66">2.600</text><text x="28" y="84.5">2.300</text><text x="28" y="103">2.000</text><text x="28" y="121">1.700</text>
    </g>
    <g fill="#ffffff">
      <rect x="38" y="85.4" width="23" height="33.6"/><rect x="65.6" y="73.2" width="23" height="45.8"/>
      <rect x="93.2" y="68.3" width="23" height="50.7"/><rect x="120.8" y="61.6" width="23" height="57.4"/>
      <rect x="148.4" y="50.6" width="23" height="68.4"/><rect x="176" y="44.5" width="23" height="74.5"/>
      <rect x="203.6" y="27.3" width="23" height="91.7"/><rect x="231.2" y="21.2" width="23" height="97.8"/>
      <rect x="258.8" y="16.4" width="23" height="102.6"/><rect x="286.4" y="12.7" width="23" height="106.3"/>
      <rect x="314" y="11.1" width="23" height="107.9"/>
    </g>
    <g stroke="#cfe3ec" stroke-width=".6" fill="none">
      <rect x="35" y="126" width="304" height="12"/>
    </g>
    <g font-size="6.5" font-style="italic" text-anchor="middle">
      <text x="49.5" y="134">2003</text><text x="77.1" y="134">2004</text><text x="104.7" y="134">2005</text>
      <text x="132.3" y="134">2006</text><text x="159.9" y="134">2007</text><text x="187.5" y="134">2008</text>
      <text x="215.1" y="134">2009</text><text x="242.7" y="134">2010</text><text x="270.3" y="134">2011</text>
      <text x="297.9" y="134">2012</text><text x="325.5" y="134">YTD2013</text>
    </g>
  </svg>
  <div class="legend-key"></div>
  <div class="legend-label">Stock</div>
  <div class="source">Source:</div>
  <div class="brand"><i></i><span>MERIDIAN<br>ESTATES</span></div>
</body>
</html>
```